Need Business Card ASAP

We need a business card design for a meeting coming up in a few days. The company name is Harlow Ridge Building and Construction and the logo is attached. Something clean, cool, and contemporary that we can get to a printer right away. Attached is the business card for Volmar Energy, an affiliated company, which we like. Instead of the hawk on the back, you could use the attached "D". We'll also be needing matching letterhead in the near future, so ideas for that are welcome.

```html
<!DOCTYPE html>
<html lang="en">
<head>
<meta charset="utf-8">
<title>Harlow Ridge Building and Construction — Business Card</title>
<link rel="stylesheet" href="https://fonts.googleapis.com/css2?family=Open+Sans:wght@400;600;700&display=swap">
<style>
  :root {
    --backdrop: #e9e4dc;
    --card-dark: #262626;
    --band-light: #d6d6d6;
    --rule-grey: #cfcfcf;
    --gold: #c4bd8c;
    --gold-deep: #a9a26e;
    --white: #ffffff;
  }
  * { margin: 0; padding: 0; box-sizing: border-box; }
  html, body {
    width: 1034px; height: 1200px; overflow: hidden;
    background: var(--backdrop);
    font-family: "Open Sans", Arial, sans-serif;
  }
  .canvas { position: relative; width: 1034px; height: 1200px; }

  /* Front of card */
  .card-front {
    position: absolute; left: 68px; top: 61px; width: 889px; height: 505px;
    background: var(--card-dark);
  }
  .band-top, .band-bottom { position: absolute; left: 0; width: 100%; background: var(--band-light); }
  .band-top { top: 0; height: 56px; }
  .band-bottom { bottom: 0; height: 51px; }

  .company-head {
    position: absolute; right: 83px; top: 78px; text-align: right;
  }
  .company-name { color: var(--gold); font-size: 27px; font-weight: 600; line-height: 1.2; }
  .company-address { color: var(--white); font-size: 19px; margin-top: 4px; }

  .divider-grey { position: absolute; left: 0; top: 160px; width: 608px; height: 8px; background: var(--rule-grey); }
  .divider-gold { position: absolute; left: 621px; top: 160px; width: 268px; height: 8px; background: var(--gold); }

  .brand-block { position: absolute; left: 37px; top: 191px; width: 200px; }
  .brand-square {
    width: 171px; height: 117px;
    background: linear-gradient(135deg, var(--gold-deep), #e2ddc0 85%);
  }
  .brand-name {
    margin-top: 14px; color: var(--gold); font-size: 16px; font-weight: 600;
    line-height: 1.25; width: 190px;
  }

  .person { position: absolute; right: 83px; top: 183px; text-align: right; }
  .person-name { color: var(--gold); font-size: 30px; font-weight: 700; line-height: 1.2; }
  .person-title { color: var(--white); font-size: 19px; font-weight: 700; margin-top: 2px; }

  .contact-list {
    position: absolute; right: 83px; top: 272px; list-style: none; text-align: right;
  }
  .contact-list li {
    color: var(--white); font-size: 22px; line-height: 38px;
    display: flex; justify-content: flex-end; align-items: center; gap: 8px;
  }
  .contact-list svg { width: 17px; height: 17px; fill: var(--rule-grey); }

  /* Back of card */
  .card-back {
    position: absolute; left: 68px; top: 608px; width: 889px; height: 507px;
    background: var(--card-dark);
  }
  .back-brand {
    position: absolute; left: 0; right: 0; top: 140px; text-align: center;
    color: var(--white); font-size: 54px; font-weight: 700; line-height: 1.15;
  }
  .back-url {
    position: absolute; left: 0; right: 0; bottom: 37px; text-align: center;
    color: var(--white); font-size: 25px; font-weight: 700; letter-spacing: 2px;
  }
</style>
</head>
<body>
<main class="canvas">
  <section class="card-front" aria-label="Business card front">
    <div class="band-top"></div>
    <header class="company-head">
      <p class="company-name">Harlow Ridge Building and Construction</p>
      <p class="company-address">00, Complex Name, Street, City 00000</p>
    </header>
    <div class="divider-grey"></div>
    <div class="divider-gold"></div>

    <div class="brand-block">
      <div class="brand-square"></div>
      <p class="brand-name">Harlow Ridge Building and Construction</p>
    </div>

    <div class="person">
      <p class="person-name">Your Name</p>
      <p class="person-title">Title</p>
    </div>

    <ul class="contact-list">
      <li>
        <svg viewBox="0 0 24 24" aria-hidden="true"><path d="M6.6 10.8a15 15 0 0 0 6.6 6.6l2.2-2.2a1 1 0 0 1 1-.25 11.4 11.4 0 0 0 3.6.57 1 1 0 0 1 1 1V20a1 1 0 0 1-1 1A17 17 0 0 1 3 4a1 1 0 0 1 1-1h3.5a1 1 0 0 1 1 1c0 1.25.2 2.45.57 3.6a1 1 0 0 1-.25 1z"/></svg>
        (123) 456-7890
      </li>
      <li>
        <svg viewBox="0 0 24 24" aria-hidden="true"><path d="M8 1h8a2 2 0 0 1 2 2v18a2 2 0 0 1-2 2H8a2 2 0 0 1-2-2V3a2 2 0 0 1 2-2zm0 3v13h8V4zm4 15a1.2 1.2 0 1 0 0 2.4A1.2 1.2 0 0 0 12 19z"/></svg>
        (123) 456-7890
      </li>
      <li>
        <svg viewBox="0 0 24 24" aria-hidden="true"><path d="M2 6h20v12H2zm2 2v.5l8 5 8-5V8l-8 5z"/></svg>
        yourname@harlowridgebuild.com
      </li>
      <li>
        <svg viewBox="0 0 24 24" aria-hidden="true"><path d="M12 2a10 10 0 1 0 0 20 10 10 0 0 0 0-20zm6.9 9h-3a15 15 0 0 0-1.3-5.6A8 8 0 0 1 18.9 11zM12 4c.9 1.2 1.8 3.6 1.9 7h-3.8c.1-3.4 1-5.8 1.9-7zM9.4 5.4A15 15 0 0 0 8.1 11h-3a8 8 0 0 1 4.3-5.6zM5.1 13h3a15 15 0 0 0 1.3 5.6A8 8 0 0 1 5.1 13zM12 20c-.9-1.2-1.8-3.6-1.9-7h3.8c-.1 3.4-1 5.8-1.9 7zm2.6-1.4a15 15 0 0 0 1.3-5.6h3a8 8 0 0 1-4.3 5.6z"/></svg>
        www.harlowridgebuild.com
      </li>
    </ul>
    <div class="band-bottom"></div>
  </section>

  <section class="card-back" aria-label="Business card back">
    <p class="back-brand">Harlow Ridge<br>Building and Construction</p>
    <p class="back-url">www.harlowridgebuild.com</p>
  </section>
</main>
</body>
</html>
```